Business Card Design

New business card design

Target Market(s)

Residential & Commercial Property Managers

Industry/Entity Type

Plumbing Services

Contact Information for Business Card

Name - Rowan Keddle, title - Director, Phone Number - 0431 286 517, email - rowan@tbk-plumbing.com.au, Company ABN - 73 215 904 386,

Font styles to use
Sans Serif

Colors
0054AA
0677BA
7BADD7
CADEEF
E8F1F8

```html
<!DOCTYPE html>
<html lang="en">
<head>
<meta charset="utf-8">
<title>TBK Plumbing Services – Business Card</title>
<link rel="stylesheet" href="https://fonts.googleapis.com/css2?family=Montserrat:wght@400;500;700;800&display=swap">
<style>
  :root {
    --backdrop: #7b7c7b;
    --card: #ffffff;
    --blue-deep: #0054AA;
    --blue: #0677BA;
    --blue-soft: #7BADD7;
    --blue-pale: #CADEEF;
    --blue-mist: #E8F1F8;
    --ink: #1d2229;
    --muted-ink: #8a8f95;
  }
  * { box-sizing: border-box; margin: 0; padding: 0; }
  html, body {
    width: 1200px; height: 1200px; overflow: hidden;
    background: var(--backdrop);
    font-family: "Montserrat", Arial, sans-serif;
  }
  .sheet {
    width: 1200px; height: 1200px;
    display: flex; align-items: center; justify-content: center; gap: 32px;
  }
  .card {
    position: relative;
    width: 560px; height: 319px;
    background: var(--card);
    overflow: hidden;
    box-shadow: 0 2px 6px rgba(0,0,0,0.18);
  }
  .card-inner {
    position: absolute; left: 0; top: 0;
    width: 478px; height: 272px;
    transform: scale(1.1715); transform-origin: 0 0;
  }
  .wave-area {
    position: absolute; left: 0; right: 0; top: 150px; bottom: 0;
  }
  .card-front .wave-area {
    background: linear-gradient(180deg, var(--blue-mist) 0%, var(--blue-pale) 55%, var(--blue-soft) 100%);
  }
  .card-back .wave-area {
    top: 162px;
    background: linear-gradient(180deg, var(--blue-mist) 0%, var(--blue-pale) 100%);
  }

  /* front */
  .brand {
    position: absolute; left: 0; right: 0; top: 62px;
    text-align: center;
  }
  .brand-name {
    display: block;
    font-weight: 500; font-size: 54px; letter-spacing: 4px;
    color: var(--ink); line-height: 1;
  }
  .brand-tagline {
    display: block; margin-top: 18px;
    font-size: 8.5px; letter-spacing: 5.2px;
    color: var(--muted-ink);
  }

  /* back */
  .person { position: absolute; left: 0; right: 0; top: 34px; text-align: center; }
  .person-name {
    font-weight: 800; font-size: 17px; letter-spacing: 0.8px;
    color: var(--blue);
  }
  .person-title {
    font-size: 12px; letter-spacing: 0.6px; color: var(--ink); margin-top: 1px;
  }
  .contact { position: absolute; left: 0; right: 0; top: 125px; text-align: center; }
  .contact-line {
    display: flex; align-items: center; justify-content: center; gap: 3px;
    font-size: 10.5px; font-weight: 500; line-height: 16px;
  }
  .contact-phone { color: var(--ink); }
  .contact-email { color: var(--blue); letter-spacing: 0.4px; }
  .contact-line svg { width: 8px; height: 8px; }
  .abn {
    position: absolute; right: 16px; top: 236px;
    font-size: 10px; font-weight: 500; color: var(--ink);
  }
</style>
</head>
<body>
<main class="sheet">
  <section class="card card-front" aria-label="Card front">
    <div class="card-inner">
      <div class="wave-area" role="img" aria-label="Flowing blue and navy wave ornament"></div>
      <div class="brand">
        <span class="brand-name">tbk</span>
        <span class="brand-tagline">plumbing services</span>
      </div>
    </div>
  </section>

  <section class="card card-back" aria-label="Card back">
    <div class="card-inner">
      <div class="wave-area" role="img" aria-label="Flowing blue and navy wave ornament"></div>
      <div class="person">
        <p class="person-name">ROWAN KEDDLE</p>
        <p class="person-title">DIRECTOR</p>
      </div>
      <div class="contact">
        <p class="contact-line contact-phone">
          <svg viewBox="0 0 8 8" aria-hidden="true"><rect x="2" y="0.5" width="4" height="7" rx="0.8" fill="none" stroke="#1d2229" stroke-width="0.9"/></svg>
          0431 286 517
        </p>
        <p class="contact-line contact-email">
          <svg viewBox="0 0 8 8" aria-hidden="true"><rect x="0.5" y="1.5" width="7" height="5" fill="#0677BA"/><path d="M0.5,1.5 L4,4.5 L7.5,1.5" fill="none" stroke="#fff" stroke-width="0.7"/></svg>
          rowan@tbk-plumbing.com.au
        </p>
      </div>
      <p class="abn">Company ABN: 73 215 904 386</p>
    </div>
  </section>
</main>
</body>
</html>
```